KVM Contracting services . Building and maintenance services, optic fibre installation

Business cards and logo design.I need a logo that I can use on business cards ,workwear and on my vehicles. I would like the KVM to be the main or larger text and contracting services to be the smaller or less important text.I like monograms, modern designs and repeating patterns symbols. I am also a Gemini and my favourite number is 22 so if this can be any inspiration to help with the design. Am thinking of the using German flag colours as a his is my family’s heritage. And the other 2 main colours I wear is black and white.But any ideas are appreciated.I do not need a design that is trade specific but a design that could be used for any business.

Target Market(s)

General public

Contact Information for Business Card

KVM Contracting Services ( front of business card)

(Back of business card)
Darren Holtwick
0451907326
Maintenance services
Optic fibre and data installation

Logo Text

Logo can just be pattern or monogram or incorporate KVM . I like the gemini star sign and the number 22

Colors
ec1f27
000000
fbee3e
ffffff

Requirements
Must have
• Logo and KVM Contracting Services on the front of business card
Nice to have
• Possible use of German flag colours.
• Modern design.
• Design to be able to be used on black or white background as I want to put it on clothing

```html
<!DOCTYPE html>
<html lang="en">
<head>
<meta charset="utf-8">
<title>KVM Contracting Services – Business Cards</title>
<link href="https://fonts.googleapis.com/css2?family=Jost:wght@500;700&family=Open+Sans:wght@400&display=swap" rel="stylesheet">
<style>
  :root {
    --backdrop: #7b7b7b;
    --card-white: #eeeeee;
    --ink: #111111;
    --rule: #9a9a9a;
    --flame-dark: #1c0808;
    --flame-red: #ff1400;
    --flame-gold: #ffb800;
  }
  html, body {
    margin: 0;
    width: 1200px;
    height: 1200px;
    overflow: hidden;
    background: var(--backdrop);
  }
  .canvas {
    position: relative;
    width: 1200px;
    height: 1200px;
  }
  .card {
    position: absolute;
    top: 310px;
    width: 366px;
    height: 594px;
    box-sizing: border-box;
  }
  .card--details {
    left: 233px;
    background: var(--card-white);
  }
  .card--brand {
    left: 628px;
    width: 369px;
    background: linear-gradient(to bottom left,
      var(--flame-dark) 0%,
      var(--flame-red) 24%,
      var(--flame-gold) 50%,
      var(--flame-red) 74%,
      var(--flame-dark) 100%);
  }
  .wordmark {
    position: absolute;
    left: 0;
    right: 0;
    text-align: center;
    color: var(--ink);
    font-family: "Jost", sans-serif;
  }
  .wordmark__name {
    display: block;
    font-weight: 700;
    font-size: 96px;
    line-height: 1;
    letter-spacing: 2px;
  }
  .wordmark__tagline {
    display: block;
    font-weight: 700;
    font-size: 22px;
    letter-spacing: 0.5px;
    margin-top: 4px;
  }
  .card--details .wordmark { top: 150px; }
  .card--brand .wordmark { top: 240px; }
  .contact {
    position: absolute;
    top: 400px;
    left: 0;
    right: 0;
    text-align: center;
    color: var(--ink);
  }
  .contact__name {
    font-family: "Jost", sans-serif;
    font-weight: 700;
    font-size: 23px;
    margin: 0;
    letter-spacing: 0.3px;
  }
  .contact__phone {
    font-family: "Open Sans", sans-serif;
    font-size: 20px;
    margin: 2px 0 0;
  }
  .contact__rule {
    width: 205px;
    height: 1px;
    border: 0;
    background: var(--rule);
    margin: 14px auto 18px;
  }
  .contact__services {
    font-family: "Open Sans", sans-serif;
    font-size: 17px;
    line-height: 21px;
    margin: 0;
  }
</style>
</head>
<body>
<main class="canvas">
  <section class="card card--details">
    <div class="wordmark">
      <span class="wordmark__name">KVM</span>
      <span class="wordmark__tagline">CONTRACTING SERVICES</span>
    </div>
    <div class="contact">
      <p class="contact__name">DARREN HOLTWICK</p>
      <p class="contact__phone">0451907326</p>
      <hr class="contact__rule">
      <p class="contact__services">Maintenance services<br>Optic fibre and data installation</p>
    </div>
  </section>
  <section class="card card--brand">
    <div class="wordmark">
      <span class="wordmark__name">KVM</span>
      <span class="wordmark__tagline">CONTRACTING SERVICES</span>
    </div>
  </section>
</main>
</body>
</html>
```